Corvane Freight Company Business Card Design

We are a company that delivers natural saltwater (from the ocean) to aquarium companies, restaurants and home marine tanks. I would like a new business card to suit.

Must include Name, company name, abn, contact number and website as well as logo (see attached).

Looking for a design that stands out, has a clean but unique appearance.

Double and single sided entries welcome

Business

• Logo

```html
<!DOCTYPE html>
<html lang="en">
<head>
<meta charset="utf-8">
<title>Corvane Freight Company – Business Card</title>
<link rel="stylesheet" href="https://fonts.googleapis.com/css2?family=Source+Sans+3:wght@400;600;700&display=swap">
<style>
  :root {
    --backdrop: #141414;
    --card-blue: #2f6ff2;
    --ink-white: #ffffff;
    --ink-soft: #e6eeff;
    --rule: rgba(255, 255, 255, 0.75);
  }
  * { margin: 0; padding: 0; box-sizing: border-box; }
  html, body {
    width: 1200px;
    height: 414px;
    overflow: hidden;
    background: var(--backdrop);
    font-family: "Source Sans 3", Arial, sans-serif;
    color: var(--ink-white);
  }
  .canvas { position: relative; width: 1200px; height: 414px; }

  .card {
    position: absolute;
    top: 53px;
    width: 525px;
    height: 299px;
    border-radius: 20px;
    background: var(--card-blue);
  }
  .card--front { left: 40px; }
  .card--back { left: 620px; }

  .brand-name {
    position: absolute;
    font-weight: 700;
    color: var(--ink-white);
    white-space: nowrap;
    text-align: center;
    line-height: 1;
  }
  .card--front .brand-name {
    left: 20px; width: 270px; top: 140px; font-size: 29px;
  }
  .card--back .brand-name {
    left: 0; width: 525px; top: 132px; font-size: 44px;
  }

  .divider {
    position: absolute;
    left: 306px; top: 58px;
    width: 2px; height: 198px;
    background: linear-gradient(to bottom, transparent, var(--rule) 15%, var(--rule) 85%, transparent);
  }

  .details { position: absolute; left: 329px; top: 74px; }
  .person { font-size: 20px; font-weight: 700; line-height: 1; }
  .person .title { font-size: 16px; font-weight: 400; }

  .contact-list { list-style: none; margin-top: 18px; font-size: 13px; line-height: 19px; color: var(--ink-soft); }
  .contact-list li { display: flex; align-items: center; gap: 5px; }
  .contact-list svg { width: 10px; height: 10px; flex: none; }

  .company { margin-top: 14px; font-size: 13px; font-weight: 700; line-height: 18px; }
  .address { font-size: 13px; line-height: 18px; color: var(--ink-soft); font-style: normal; }

  .web-address {
    position: absolute;
    left: 0; width: 525px; top: 238px;
    text-align: center;
    font-size: 16px;
    letter-spacing: 3px;
    color: var(--ink-soft);
  }
</style>
</head>
<body>
<main class="canvas">
  <section class="card card--front" aria-label="Card front">
    <p class="brand-name">Corvane Freight</p>
    <div class="divider"></div>
    <div class="details">
      <p class="person">Your name, <span class="title">Title</span></p>
      <ul class="contact-list">
        <li>
          <svg viewBox="0 0 10 10" aria-hidden="true"><circle cx="5" cy="5" r="4.3" fill="none" stroke="#fff" stroke-width="1"/><path d="M3.4 2.8 L4.3 2.6 L4.7 3.9 L4.1 4.4 Q4.6 5.5 5.6 6 L6.1 5.4 L7.3 5.8 L7.1 6.7 Q5.2 7 3.9 5.5 Q3.1 4.3 3.4 2.8Z" fill="#fff"/></svg>
          123-456-7890
        </li>
        <li>
          <svg viewBox="0 0 10 10" aria-hidden="true"><circle cx="5" cy="5" r="4.5" fill="#fff"/><path d="M0.8 5 H9.2 M5 0.6 Q2.6 5 5 9.4 M5 0.6 Q7.4 5 5 9.4" stroke="var(--card-blue)" stroke-width="0.8" fill="none"/></svg>
          www.website.com
        </li>
        <li>ABN : 0123456789</li>
      </ul>
      <p class="company">Corvane Freight Company</p>
      <address class="address">Street Name, City Name<br>State, City Zip Code</address>
    </div>
  </section>

  <section class="card card--back" aria-label="Card back">
    <p class="brand-name">Corvane Freight</p>
    <p class="web-address">www.website.com</p>
  </section>
</main>
</body>
</html>
```